NimbaVault Website Homepage Design

Please provide your idea of homepage for a hosting company. This project is for DESIGN only, no coding.

It must use/combine colors used in logo, clean, modern look.

Homepage must consist of at least 4 sections (example: testimonials, services, and so on. not necesarily all of them). We would like the navigation to be horizontal, but not mandatory.

You can include a preview of services page (optional, not a must).

Number of Pages Required

1 page

Font styles to use
Sans Serif

```html
<!DOCTYPE html>
<html lang="en">
<head>
<meta charset="utf-8">
<title>NimbaVault — Hosting</title>
<link href="https://fonts.googleapis.com/css2?family=Poppins:wght@300;400;500;600&family=Roboto+Condensed:wght@700&family=Rubik:wght@500;600&display=swap" rel="stylesheet">
<style>
:root{
  --blue:#2a8fd0;
  --blue-deep:#0f6fb5;
  --blue-pale:#e4f2fb;
  --navy:#0b1a2e;
  --navy-2:#1b3a5e;
  --ink:#1d1d1f;
  --muted:#6b6b6b;
  --line:#e6e6e6;
  --white:#ffffff;
}
*{margin:0;padding:0;box-sizing:border-box}
html,body{width:1200px;height:4112px;overflow:hidden}
body{position:relative;font-family:"Poppins",sans-serif;color:var(--ink);background:var(--white)}
.abs{position:absolute}
.backdrop{position:absolute;left:0;top:0}
.heading{font-family:"Roboto Condensed",sans-serif;font-weight:700;font-size:26px;text-align:center}

/* nav */
.nav{left:115px;top:0;width:970px;height:77px;background:var(--white);border-radius:0 0 10px 10px;display:flex;align-items:center;padding:0 30px;box-shadow:0 4px 14px rgba(0,0,0,.12)}
.brand{font-family:"Poppins",sans-serif;font-weight:500;font-size:34px;color:var(--blue);letter-spacing:1px;display:flex;align-items:center;gap:10px}
.brand-dot{width:14px;height:14px;background:var(--blue);border-radius:50%}
.menu{margin-left:auto;display:flex;gap:31px;font-size:11px;color:#444;align-items:center}
.menu .on{color:var(--blue)}

/* hero */
.hero-title{left:59px;top:272px;font-family:"Rubik",sans-serif;font-weight:600;font-size:54px;line-height:70px;color:var(--white)}
.hero-title span{color:var(--blue)}
.btn{display:flex;align-items:center;justify-content:center;font-size:15px;font-weight:500}
.btn-solid{background:var(--blue);color:var(--white)}
.btn-ghost{background:var(--white);color:var(--blue)}

/* feature cards */
.feature{background:var(--white);border-radius:6px;box-shadow:0 4px 16px rgba(0,0,0,.14);text-align:center;padding:22px 18px 0}
.feature.active{background:var(--blue);color:var(--white)}
.feature h3{font-weight:400;font-size:18px;line-height:26px;margin:18px 0 14px}
.feature p{font-size:11.5px;line-height:19px;color:var(--muted)}
.feature.active p{color:#eaf5ff}

/* about */
.about h2{font-family:"Roboto Condensed",sans-serif;font-size:26px}
.about h4{font-weight:400;font-size:18px;color:var(--blue);margin:26px 0 18px}
.about p{font-size:12px;line-height:19.5px;color:var(--muted);margin-bottom:10px}

/* testimonial */
.quote-box{background:rgba(255,255,255,.14);border-radius:26px;color:var(--white);text-align:center;padding:40px 26px 0;font-size:12px;line-height:19.5px}
.portrait{border:5px solid var(--white);border-radius:26px;background:linear-gradient(160deg,#c9c4bc,#6f5a48)}

/* platforms */
.platform{border:1px solid #eef0f2;box-shadow:0 2px 10px rgba(0,0,0,.05);text-align:center;padding-top:28px}
.platform .ghost{font-size:22px;font-weight:600;color:#d5e9f7;margin-top:14px}
.platform .name{font-size:15px;margin-top:-4px}
.platform .go{width:34px;height:34px;border-radius:50%;background:var(--blue);margin:28px auto 0;display:flex;align-items:center;justify-content:center}

/* domain */
.search{left:262px;top:2662px;width:675px;height:56px;background:var(--white);display:flex;align-items:center;padding:0 12px 0 16px;font-size:13px;color:#777}
.search .tld{margin-left:auto;border-left:1px solid #ccc;padding-left:10px;margin-right:16px;color:#333}
.search .go{background:var(--blue);color:var(--white);font-size:13px;font-weight:500;width:146px;height:36px;display:flex;align-items:center;justify-content:center}
.prices{left:0;top:2756px;width:1200px;display:flex;justify-content:center;gap:56px;color:var(--white);font-size:14px}

/* pricing */
.plan{border:1px solid #e2e2e2;text-align:center;background:var(--white)}
.plan h3{font-weight:400;font-size:18px;color:var(--blue);margin-top:26px;height:40px}
.plan .price{height:36px;background:var(--blue-pale);font-size:30px;font-weight:600;line-height:36px}
.plan .price span{color:var(--blue);font-weight:400}
.plan.featured .price{background:var(--blue)}
.plan.featured .price span{color:var(--white)}
.plan ul{list-style:none;margin:12px 24px 0}
.plan li{height:38px;line-height:38px;border-bottom:1px solid var(--line);font-size:11.5px;color:var(--muted)}
.plan li::before{content:"✓";color:var(--blue);font-weight:600;font-size:15px;margin-right:6px}
.plan .cta{width:146px;height:36px;margin:28px auto 0;background:var(--blue);color:var(--white);font-size:13px;font-weight:600;display:flex;align-items:center;justify-content:center}

/* footer */
.foot-brand{left:59px;top:3745px;font-size:34px;font-weight:500;color:var(--white);letter-spacing:1px;display:flex;align-items:center;gap:10px}
.foot-brand .brand-dot{background:var(--white)}
.socials{left:59px;top:3828px;display:flex;gap:7px}
.socials i{width:32px;height:32px;border:2px solid var(--white);border-radius:50%;display:block}
.socials i:first-child{background:var(--white)}
.col h4{font-size:23px;font-weight:400;color:var(--blue);margin-bottom:12px}
.col li{list-style:none;font-size:12px;color:#dfe6ee;height:31.5px}
.contact-row{display:flex;gap:14px;margin-bottom:20px;font-size:13px;color:var(--white);line-height:20px}
.contact-row u{font-size:12px}
.copy{left:0;top:4095px;width:1200px;height:17px;background:var(--blue);color:var(--white);font-size:10.5px;text-align:center;line-height:17px}
</style>
</head>
<body>

<svg class="backdrop" width="1200" height="4112" viewBox="0 0 1200 4112">
  <defs>
    <linearGradient id="heroGrad" x1="0" y1="0" x2="1" y2="1">
      <stop offset="0" stop-color="#152c47"/><stop offset=".6" stop-color="#0c1c30"/><stop offset="1" stop-color="#1f3d5e"/>
    </linearGradient>
    <linearGradient id="bandGrad" x1="0" y1="0" x2="1" y2="1">
      <stop offset="0" stop-color="#1b8ed3"/><stop offset="1" stop-color="#0a76bf"/>
    </linearGradient>
    <linearGradient id="footGrad" x1="0" y1="0" x2="0" y2="1">
      <stop offset="0" stop-color="#0a1526"/><stop offset="1" stop-color="#101d30"/>
    </linearGradient>
  </defs>
  <g role="img" aria-label="Hero photo: woman holding a laptop in a data centre aisle">
    <path d="M0 0H1200V565C1000 560 850 610 700 640C500 680 300 640 150 650C80 655 30 665 0 672Z" fill="url(#heroGrad)"/>
    <rect x="760" y="90" width="260" height="430" rx="120" fill="#2b2a30" opacity=".55"/>
  </g>
  <g role="img" aria-label="Server room photo tinted blue behind testimonials">
    <path d="M0 1462C250 1405 500 1430 700 1452C900 1474 1050 1450 1200 1432V2078C1000 2075 820 2000 620 1948C420 1898 220 1870 0 1905Z" fill="url(#bandGrad)"/>
  </g>
  <g role="img" aria-label="Photo of technicians in a data centre tinted blue behind domain search">
    <path d="M0 2570C280 2470 520 2560 800 2520C1000 2492 1100 2492 1200 2482V3072C1000 3070 820 2965 620 2932C420 2900 220 2872 0 2898Z" fill="url(#bandGrad)"/>
  </g>
  <g role="img" aria-label="Dark server room photo behind footer">
    <path d="M0 3720C280 3640 520 3725 800 3692C1000 3670 1100 3652 1200 3650V4112H0Z" fill="url(#footGrad)"/>
  </g>
  <path role="img" aria-label="Photo of two engineers working at a server rack" d="M760 930C880 905 1000 960 1060 1040C1110 1110 1070 1200 1000 1260C930 1320 820 1345 745 1300C680 1260 680 1150 690 1060C700 980 710 942 760 930Z" fill="#2e6fb8"/>
</svg>

<header class="abs nav">
  <div class="brand">NimbaVault<span class="brand-dot"></span></div>
  <nav class="menu">
    <span class="on">HOME</span><span>ABOUT US</span><span>HOSTING</span><span>PRICING PLAN</span><span>TESTIMONIALS</span><span>CONTACT US</span>
    <svg width="14" height="14" viewBox="0 0 14 14"><circle cx="6" cy="6" r="4.5" fill="none" stroke="#2a8fd0" stroke-width="1.6"/><path d="M9.5 9.5L13 13" stroke="#2a8fd0" stroke-width="1.6"/></svg>
  </nav>
</header>

<h1 class="abs hero-title"><span>Best Hosting</span> Company<br>Establishment</h1>
<div class="abs btn btn-solid" style="left:61px;top:426px;width:129px;height:35px">Read More</div>
<div class="abs btn btn-ghost" style="left:201px;top:426px;width:131px;height:35px">Get In Touch</div>

<div class="abs feature active" style="left:124px;top:624px;width:211px;height:231px">
  <svg width="36" height="42" viewBox="0 0 36 42" fill="none" stroke="#fff" stroke-width="1.6"><rect x="2" y="2" width="32" height="38" rx="2"/><rect x="7" y="8" width="8" height="8"/><rect x="21" y="8" width="8" height="8"/><rect x="7" y="22" width="8" height="8"/><rect x="21" y="22" width="8" height="8"/></svg>
  <h3>SSD Persistent<br>Storage</h3>
  <p>Lorem ipsum dolor sit amet, consectetur adipiscing elit. Ut elit tellus.</p>
</div>
<div class="abs feature" style="left:365px;top:638px;width:210px;height:233px">
  <svg width="48" height="38" viewBox="0 0 48 38" fill="none" stroke="#2a8fd0" stroke-width="1.6"><rect x="2" y="2" width="44" height="28" rx="2"/><circle cx="24" cy="16" r="6"/><path d="M16 36H32M24 30V36"/></svg>
  <h3>Technical<br>Superiority</h3>
  <p>Lorem ipsum dolor sit amet, consectetur adipiscing elit. Ut elit tellus.</p>
</div>
<div class="abs feature" style="left:605px;top:586px;width:211px;height:233px">
  <svg width="46" height="42" viewBox="0 0 46 42" fill="none" stroke="#2a8fd0" stroke-width="1.6"><path d="M12 28H9A7 7 0 0 1 10 14A11 11 0 0 1 32 12A8 8 0 0 1 37 28H34"/><path d="M23 18V40M16 24V34M30 24V34"/><circle cx="23" cy="40" r="1.5"/></svg>
  <h3>Ultra-Fast<br>Network</h3>
  <p>Lorem ipsum dolor sit amet, consectetur adipiscing elit. Ut elit tellus.</p>
</div>
<div class="abs feature" style="left:844px;top:541px;width:211px;height:233px">
  <svg width="46" height="42" viewBox="0 0 46 42" fill="none" stroke="#2a8fd0" stroke-width="1.6"><rect x="4" y="4" width="38" height="30" rx="3"/><circle cx="23" cy="19" r="6"/><circle cx="23" cy="19" r="2"/><path d="M14 40H32"/></svg>
  <h3>Fully-Managed<br>Service</h3>
  <p>Lorem ipsum dolor sit amet, consectetur adipiscing elit. Ut elit tellus.</p>
</div>

<section class="abs about" style="left:121px;top:963px;width:420px">
  <h2>About Us</h2>
  <h4>Grow Your Website Traffic With Us</h4>
  <p>It is a long established fact that a reader will be distracted by the readable content of a page when looking at its layout. The point of using Lorem Ipsum is that it has a more-or-less normal distribution of letters, as opposed to using 'Content here, content here', making it look like readable English.</p>
  <p>It is a long established fact that a reader will be distracted by the readable content of a page when looking at its layout. The point of using Lorem Ipsum is that it has a more-or-less normal distribution of letters, as opposed to using 'Content here, content here', making it look like readable English.</p>
</section>
<div class="abs btn btn-solid" style="left:120px;top:1299px;width:131px;height:36px">Read More</div>

<h2 class="abs heading" style="left:0;top:1512px;width:1200px;color:#fff">Testimonials</h2>
<div class="abs portrait" style="left:200px;top:1590px;width:185px;height:183px" role="img" aria-label="Customer portrait"></div>
<div class="abs quote-box" style="left:404px;top:1590px;width:597px;height:183px">
  <svg width="48" height="36" viewBox="0 0 48 36" fill="none" stroke="#fff" stroke-width="2"><path d="M20 4C8 6 2 14 2 24A8 8 0 1 0 10 16"/><path d="M44 4C32 6 26 14 26 24A8 8 0 1 0 34 16"/></svg>
  <p style="margin-top:10px">There are many variations of passages of Lorem Ipsum available, but the majority have suffered alteration in some form, by injected humour, or randomised words which don't look even slightly believable. If you are going to use a passage of Lorem Ipsum, you need to be sure there isn't anything embarrassing hidden in the middle of text.</p>
</div>
<svg class="abs" style="left:602px;top:1795px" width="88" height="20" viewBox="0 0 88 20" fill="none" stroke="#fff" stroke-width="2"><path d="M2 10H36M10 3L2 10L10 17"/><path d="M50 10H86M78 3L86 10L78 17"/></svg>

<h2 class="abs heading" style="left:0;top:2068px;width:1200px">Web Hosting Platform</h2>
<div class="abs platform" style="left:109px;top:2150px;width:223px;height:239px">
  <svg width="40" height="38" viewBox="0 0 40 38" fill="none" stroke="#2a8fd0" stroke-width="1.6"><rect x="4" y="2" width="32" height="10"/><rect x="4" y="14" width="32" height="10"/><path d="M20 24V32M8 32H32M8 32V36M32 32V36M20 32V36"/></svg>
  <div class="ghost">Shared</div><div class="name">Shared Hosting</div>
  <div class="go"><svg width="10" height="10" viewBox="0 0 10 10"><path d="M3 1L7 5L3 9" stroke="#fff" stroke-width="2" fill="none"/></svg></div>
</div>
<div class="abs platform" style="left:364px;top:2150px;width:223px;height:239px;box-shadow:0 4px 14px rgba(0,0,0,.1)">
  <svg width="40" height="38" viewBox="0 0 40 38" fill="none" stroke="#2a8fd0" stroke-width="1.6"><rect x="4" y="2" width="24" height="32"/><path d="M8 8H24M8 14H24M8 20H24"/><rect x="22" y="20" width="16" height="14" fill="#fff"/></svg>
  <div class="ghost">Dedicated</div><div class="name">Dedicated Hosting</div>
  <div class="go"><svg width="10" height="10" viewBox="0 0 10 10"><path d="M3 1L7 5L3 9" stroke="#fff" stroke-width="2" fill="none"/></svg></div>
</div>
<div class="abs platform" style="left:611px;top:2150px;width:224px;height:239px">
  <svg width="40" height="38" viewBox="0 0 40 38" fill="none" stroke="#2a8fd0" stroke-width="1.6"><path d="M10 26A7 7 0 0 1 10 12A10 10 0 0 1 30 11A8 8 0 0 1 30 26Z"/><circle cx="20" cy="20" r="4"/><path d="M20 26V34M12 34H28"/></svg>
  <div class="ghost">Cloud</div><div class="name">Cloud Hosting</div>
  <div class="go"><svg width="10" height="10" viewBox="0 0 10 10"><path d="M3 1L7 5L3 9" stroke="#fff" stroke-width="2" fill="none"/></svg></div>
</div>
<div class="abs platform" style="left:867px;top:2150px;width:223px;height:239px">
  <svg width="40" height="38" viewBox="0 0 40 38" fill="none" stroke="#2a8fd0" stroke-width="1.6"><rect x="2" y="4" width="30" height="24"/><path d="M2 10H32"/><circle cx="30" cy="26" r="6" fill="#fff"/><path d="M34 30L38 34"/></svg>
  <div class="ghost">Domain</div><div class="name">Domain Checker</div>
  <div class="go"><svg width="10" height="10" viewBox="0 0 10 10"><path d="M3 1L7 5L3 9" stroke="#fff" stroke-width="2" fill="none"/></svg></div>
</div>

<h2 class="abs heading" style="left:0;top:2577px;width:1200px;color:#fff">Find Your Perfect Domain Name</h2>
<div class="abs search"><span>Find Your Domain</span><span class="tld">.com</span><span class="go">SEARCH NOW</span></div>
<div class="abs prices"><span>.Com Only $8.88</span><span>.Co Only $9.88</span><span>.Info Only $9.70</span><span>.Net Only $7.80</span></div>

<h2 class="abs heading" style="left:0;top:3055px;width:1200px">Pricing Plan</h2>
<div class="abs plan" style="left:131px;top:3120px;width:292px;height:388px">
  <h3>Cloud Hosting</h3><div class="price">$50 <span>/m</span></div>
  <ul><li>Brandwidth: 2GB</li><li>Clint &amp; Product: 500+</li><li>onlinespace: 500MB</li><li>Domain: 2</li><li>Hidden Fees: 0</li></ul>
  <div class="cta">DISCOVER MORE</div>
</div>
<div class="abs plan featured" style="left:455px;top:3120px;width:290px;height:388px">
  <h3>Pressly Hosting</h3><div class="price">$50 <span>/m</span></div>
  <ul><li>Brandwidth: 2GB</li><li>Clint &amp; Product: 500+</li><li>onlinespace: 500MB</li><li>Domain: 2</li><li>Hidden Fees: 0</li></ul>
  <div class="cta">DISCOVER MORE</div>
</div>
<div class="abs plan" style="left:777px;top:3120px;width:291px;height:388px">
  <h3>VPS Hosting</h3><div class="price">$50 <span>/m</span></div>
  <ul><li>Brandwidth: 2GB</li><li>Clint &amp; Product: 500+</li><li>onlinespace: 500MB</li><li>Domain: 2</li><li>Hidden Fees: 0</li></ul>
  <div class="cta">DISCOVER MORE</div>
</div>

<div class="abs foot-brand">NimbaVault<span class="brand-dot"></span></div>
<div class="abs socials" aria-label="Social links"><i></i><i></i><i></i><i></i><i></i></div>

<div class="abs col" style="left:338px;top:3742px">
  <h4>Links</h4>
  <ul><li>- Home</li><li>- Hosting</li><li>- About Us</li><li>- Pricing Plan</li><li>- Testimonials</li><li>- Contact Us</li></ul>
</div>
<div class="abs col" style="left:613px;top:3742px">
  <h4>Hosting</h4>
  <ul><li>- Dedicated Hosting</li><li>- Shared Hosting</li><li>- VPS Hosting</li><li>- Pressly Hosting</li><li>- Cloud Hosting</li><li>- Domain Checker</li></ul>
</div>
<div class="abs col" style="left:889px;top:3742px;width:260px">
  <h4>Contact Us</h4>
  <div class="contact-row">
    <svg width="20" height="20" viewBox="0 0 20 20" fill="none" stroke="#2a8fd0" stroke-width="1.5"><path d="M4 2L8 6L6 8C7 11 9 13 12 14L14 12L18 16L16 18C9 18 2 11 2 4Z"/></svg>
    <div><u>Call</u><br>+123 456 7890</div>
  </div>
  <div class="contact-row">
    <svg width="20" height="16" viewBox="0 0 20 16" fill="none" stroke="#2a8fd0" stroke-width="1.5"><rect x="1" y="1" width="18" height="14"/><path d="M1 1L10 9L19 1"/></svg>
    <div><u>Mail</u><br>info@nimbavault.com</div>
  </div>
  <div class="contact-row">
    <svg width="16" height="22" viewBox="0 0 16 22" fill="none" stroke="#2a8fd0" stroke-width="1.5"><path d="M8 21C3 14 1 10 1 7A7 7 0 0 1 15 7C15 10 13 14 8 21Z"/><circle cx="8" cy="7" r="2.5"/></svg>
    <div><u>Location</u><br><span style="font-size:12px">120- Lorem ipsum is dummy<br>printing industry</span></div>
  </div>
</div>

<div class="abs copy">© NimbaVault 2021 - All Right Reserved.</div>

</body>
</html>
```